Business Card Design Project

We are a construction company in Orange County, CA. We need a two sided business card. We would like the back to be our logo with web URL. Front should included Name, title, address, phone, fax and email address.

our address is
627 West Dorrance Blvd, Suite 308
Larkmoor, CO 92718

Our logo files are attached.

Construction

```html
<!DOCTYPE html>
<html lang="en">
<head>
<meta charset="utf-8">
<title>Braxton Business Card</title>
<link href="https://fonts.googleapis.com/css2?family=Open+Sans:wght@400;700;800&display=swap" rel="stylesheet">
<style>
  :root {
    --brand-blue: #1b4a7c;
    --swoosh-grey: #8a8d91;
    --card-white: #ffffff;
    --ink: #3d4249;
    --divider: #6d7278;
    --backdrop: #e8e5e0;
  }
  html, body {
    margin: 0;
    padding: 0;
    width: 1200px;
    height: 402px;
    overflow: hidden;
    background: var(--backdrop);
    font-family: "Open Sans", sans-serif;
  }
  .canvas {
    position: relative;
    width: 1200px;
    height: 402px;
  }
  .card {
    position: absolute;
    top: 57px;
    width: 523px;
    height: 298px;
    border-radius: 24px;
    overflow: hidden;
  }
  .card--front { left: 65px; background: var(--card-white); }
  .card--back { left: 647px; background: var(--brand-blue); }

  .front-swoosh {
    position: absolute;
    inset: 0;
  }
  .holder {
    position: absolute;
    right: 34px;
    top: 30px;
    text-align: right;
    color: var(--card-white);
  }
  .holder__name {
    font-weight: 700;
    font-size: 19px;
    line-height: 1.1;
  }
  .holder__title {
    font-size: 15px;
    line-height: 1.35;
  }
  .company-name {
    position: absolute;
    margin: 0;
    font-weight: 800;
    letter-spacing: -1px;
    line-height: 1;
  }
  .card--front .company-name {
    left: 22px;
    top: 80px;
    font-size: 62px;
    color: var(--brand-blue);
  }
  .card--back .company-name {
    left: 0;
    right: 0;
    top: 108px;
    text-align: center;
    font-size: 70px;
    color: var(--card-white);
  }
  .contact {
    position: absolute;
    left: 30px;
    top: 218px;
    display: flex;
    font-size: 13px;
    color: var(--ink);
    line-height: 18px;
  }
  .contact__list {
    list-style: none;
    margin: 0;
    padding: 0 12px 0 0;
  }
  .contact__list li {
    display: flex;
    align-items: center;
    gap: 6px;
  }
  .contact__icon {
    width: 10px;
    height: 10px;
    fill: var(--brand-blue);
  }
  .contact__address {
    margin: 22px 0 0;
    padding-left: 10px;
    border-left: 1px solid var(--divider);
    font-style: normal;
  }
</style>
</head>
<body>
<main class="canvas">
  <section class="card card--front" aria-label="Business card front">
    <svg class="front-swoosh" viewBox="0 0 523 298" width="523" height="298" aria-hidden="true">
      <path d="M0,0 H523 V134 C430,80 270,24 0,20 Z" fill="var(--brand-blue)"/>
      <path d="M0,38 C80,16 200,14 330,72" fill="none" stroke="var(--swoosh-grey)" stroke-width="5" stroke-linecap="round"/>
    </svg>
    <div class="holder">
      <div class="holder__name">Your name</div>
      <div class="holder__title">Title</div>
    </div>
    <h1 class="company-name">BRAXTON</h1>
    <div class="contact">
      <ul class="contact__list">
        <li>
          <svg class="contact__icon" viewBox="0 0 10 10" aria-hidden="true"><circle cx="5" cy="5" r="5"/><path d="M3,2.5 L4,2.5 L4.5,4 L3.8,4.6 C4.2,5.5 4.6,6 5.4,6.3 L6,5.6 L7.5,6.1 L7.5,7.2 C5,7.5 2.6,5 3,2.5 Z" fill="#fff"/></svg>
          01-987-6543
        </li>
        <li>
          <svg class="contact__icon" viewBox="0 0 10 10" aria-hidden="true"><rect x="2.5" y="1" width="5" height="3"/><rect x="0.5" y="4" width="9" height="4" rx="1"/><rect x="2.5" y="6.5" width="5" height="3"/></svg>
          01-987-6543
        </li>
        <li>
          <svg class="contact__icon" viewBox="0 0 10 10" aria-hidden="true"><rect x="0.5" y="2" width="9" height="6"/><path d="M0.5,2 L5,5.5 L9.5,2" fill="none" stroke="#fff" stroke-width="0.9"/></svg>
          info@braxtonbuild.com
        </li>
        <li>
          <svg class="contact__icon" viewBox="0 0 10 10" aria-hidden="true"><circle cx="5" cy="5" r="4.8"/><path d="M0.5,5 H9.5 M5,0.5 C2.5,3 2.5,7 5,9.5 M5,0.5 C7.5,3 7.5,7 5,9.5" fill="none" stroke="#fff" stroke-width="0.7"/></svg>
          www.braxtonbuild.com
        </li>
      </ul>
      <address class="contact__address">
        627 West Dorrance Blvd<br>
        Suite 308 Larkmoor, CO 92718
      </address>
    </div>
  </section>

  <section class="card card--back" aria-label="Business card back">
    <h2 class="company-name">BRAXTON</h2>
  </section>
</main>
</body>
</html>
```